Redesign of business card for Cedar Ridge Mechanical

We are looking for a new design for our business cards for Cedar Ridge Mechanical. We are a plumbing & HVAC construction company, operating on the West Coast of Canada and USA. Logo attached.
Industry/Entity Type
Construction - Plumbing & HVAC
Contact Information for Business Card
Name, address, phone numbers, email, website address
Look and feel
Each slider illustrates characteristics of the customer's brand and the style your logo design should communicate.

```html
<!DOCTYPE html>
<html lang="en">
<head>
<meta charset="utf-8">
<title>Cedar Ridge Mechanical – Business Card</title>
<link rel="stylesheet" href="https://fonts.googleapis.com/css2?family=Poppins:wght@300;400;600&display=swap">
<style>
  :root {
    --backdrop: #232323;
    --card: #1e1e20;
    --card-edge: #2a2a2d;
    --ink: #ffffff;
    --ink-soft: #cfcfcf;
    --ghost: #29292c;
  }
  * { box-sizing: border-box; margin: 0; padding: 0; }
  html, body {
    width: 1200px; height: 780px; overflow: hidden;
    background: var(--backdrop);
    font-family: "Poppins", sans-serif;
    color: var(--ink);
  }
  .canvas {
    position: relative; width: 1200px; height: 780px;
    display: flex; align-items: center; justify-content: center; gap: 60px;
  }
  .card {
    position: relative; background: var(--card);
    border-radius: 22px; overflow: hidden;
    box-shadow: 0 0 0 1px var(--card-edge);
  }
  /* contact side */
  .card--back { width: 340px; height: 580px; padding: 36px 30px; }
  .card--back .ghost-mark {
    position: absolute; right: -70px; bottom: -70px;
    width: 320px; height: 320px;
    border: 34px solid var(--ghost); border-radius: 30px;
  }
  .brand { display: flex; align-items: center; gap: 10px; }
  .brand__square { width: 14px; height: 14px; background: var(--ink); flex: none; }
  .brand__name { font-weight: 600; letter-spacing: 0.04em; text-transform: uppercase; }
  .card--back .brand__name { font-size: 15px; }
  .person { margin-top: 46px; border-left: 4px solid var(--ink); padding-left: 10px; }
  .person__name { font-size: 24px; line-height: 1.1; }
  .person__first { font-weight: 600; }
  .person__last { font-weight: 300; }
  .person__title { font-size: 12px; font-weight: 300; color: var(--ink-soft); margin-top: 4px; }
  .address { margin-top: 30px; font-size: 12px; font-weight: 300; color: var(--ink-soft); line-height: 1.6; }
  .contact-list { list-style: none; margin-top: 18px; font-size: 12px; font-weight: 300; color: var(--ink-soft); }
  .contact-list li { display: flex; align-items: center; gap: 8px; line-height: 1.9; }
  .contact-list svg { width: 11px; height: 11px; fill: var(--ink); flex: none; }
  /* logo side */
  .card--front {
    width: 560px; height: 330px;
    display: flex; align-items: center; justify-content: center;
  }
  .card--front .brand { gap: 16px; }
  .card--front .brand__square { width: 26px; height: 26px; }
  .card--front .brand__name { font-size: 30px; }
</style>
</head>
<body>
<main class="canvas">
  <section class="card card--back" aria-label="Contact side">
    <div class="ghost-mark" aria-hidden="true"></div>
    <div class="brand">
      <span class="brand__square"></span>
      <span class="brand__name">Cedar Ridge Mechanical</span>
    </div>
    <div class="person">
      <p class="person__name"><span class="person__first">Marta</span> <span class="person__last">Lindqvist</span></p>
      <p class="person__title">Founder &amp; CEO</p>
    </div>
    <p class="address">418 Harbor Ave. Suite 120<br>Bellingham, WA 98225</p>
    <ul class="contact-list">
      <li><svg viewBox="0 0 24 24"><path d="M6.6 10.8a15.1 15.1 0 0 0 6.6 6.6l2.2-2.2a1 1 0 0 1 1-.25 11.4 11.4 0 0 0 3.6.57 1 1 0 0 1 1 1V20a1 1 0 0 1-1 1A17 17 0 0 1 3 4a1 1 0 0 1 1-1h3.5a1 1 0 0 1 1 1c0 1.25.2 2.45.57 3.57a1 1 0 0 1-.25 1z"/></svg>(360) 555-0147</li>
      <li><svg viewBox="0 0 24 24"><path d="M2 5h20v14H2zm2 2v.5l8 5 8-5V7z"/></svg>info@cedarridgemech.com</li>
      <li><svg viewBox="0 0 24 24"><circle cx="12" cy="12" r="10"/></svg>www.cedarridgemech.com</li>
    </ul>
  </section>
  <section class="card card--front" aria-label="Logo side">
    <div class="brand">
      <span class="brand__square"></span>
      <span class="brand__name">Cedar Ridge Mechanical</span>
    </div>
  </section>
</main>
</body>
</html>
```